VENTURE CAPITAL GROUP BUSINESS CARD DESIGN

Venture Capital Group based in SF looking for a bold business card design. No trendy colour explosion, 3D effects etc. Just "simple" optical effects. Works on your brain, keeps your eye focused and sticks to your mind.
Target Market(s)
Technology startups
Industry/Entity Type
Venture Capital
Contact Information for Business Card
DESMOND WHITLAKE
MANAGING PARTNER
187 FENWORTH ST SAN FRANCISCO, CA 94187
415.555.0142 O
415.555.0147 F
415.555.0193 C
desmond@veldtmoorcapital.ventures

```html
<!DOCTYPE html>
<html lang="en">
<head>
<meta charset="utf-8">
<title>Veldtmoor Capital – Business Card</title>
<link rel="stylesheet" href="https://fonts.googleapis.com/css2?family=Cinzel:wght@400&family=EB+Garamond:wght@400;600&display=swap">
<style>
  :root {
    --page: #e9e9e7;
    --card: #fbfbfb;
    --card-edge: #e2e2e2;
    --green: #2fae4e;
    --green-dark: #1f9a3e;
    --ink: #5b5b5b;
    --ink-soft: #7a7a7a;
  }
  * { box-sizing: border-box; margin: 0; padding: 0; }
  html, body {
    width: 1200px; height: 1023px; overflow: hidden;
    background: var(--page);
  }
  .card {
    position: absolute; left: 75px; top: 211px;
    width: 1050px; height: 600px;
    background: var(--card);
    border: 1px solid var(--card-edge);
    box-shadow: 0 10px 30px rgba(0,0,0,0.12);
  }
  .brand {
    position: absolute; left: 560px; top: 120px;
    display: flex; align-items: center; gap: 18px;
    font-family: "EB Garamond", serif; font-weight: 400;
    font-size: 44px; color: var(--green);
  }
  .brand-dot {
    width: 30px; height: 30px; border-radius: 50%;
    background: var(--green);
  }
  .holder {
    position: absolute; left: 70px; top: 250px;
  }
  .holder-name {
    font-family: "Cinzel", serif; font-weight: 400;
    font-size: 38px; color: var(--green); letter-spacing: 1px;
  }
  .holder-title {
    margin-top: 4px;
    font-family: "EB Garamond", serif; font-size: 22px;
    color: var(--ink-soft);
  }
  .contacts {
    position: absolute; left: 300px; top: 380px;
    list-style: none;
    font-family: "EB Garamond", serif; font-size: 22px; color: var(--ink);
  }
  .contacts li {
    display: flex; align-items: center; gap: 14px;
    height: 38px;
  }
  .icon {
    width: 26px; height: 26px; flex: none;
  }
  .address {
    position: absolute; left: 300px; top: 540px;
    font-family: "EB Garamond", serif; font-weight: 600;
    font-size: 24px; color: var(--green-dark);
  }
</style>
</head>
<body>
<main class="card">
  <div class="brand"><span class="brand-dot"></span>Veldtmoor Capital</div>

  <div class="holder">
    <h1 class="holder-name">Desmond Whitlake</h1>
    <p class="holder-title">Founder/ Owner</p>
  </div>

  <ul class="contacts">
    <li>
      <svg class="icon" viewBox="0 0 26 26" aria-hidden="true"><circle cx="13" cy="13" r="13" fill="var(--green)"/><path d="M7 11c0-2 2.5-3 6-3s6 1 6 3l-2 1-1-2h-6l-1 2z M9 13h8l1 5H8z" fill="#fff"/></svg>
      415.555.0142
    </li>
    <li>
      <svg class="icon" viewBox="0 0 26 26" aria-hidden="true"><circle cx="13" cy="13" r="13" fill="var(--green)"/><rect x="9" y="6" width="8" height="5" fill="#fff"/><rect x="6" y="11" width="14" height="6" rx="1" fill="#fff"/><rect x="9" y="16" width="8" height="4" fill="#fff"/></svg>
      415.555.0147
    </li>
    <li>
      <svg class="icon" viewBox="0 0 26 26" aria-hidden="true"><circle cx="13" cy="13" r="13" fill="var(--green)"/><path d="M9 6l3 3-2 2c1 2 3 4 5 5l2-2 3 3-2 3c-5 0-11-6-11-11z" fill="#fff"/></svg>
      415.555.0193
    </li>
    <li>
      <svg class="icon" viewBox="0 0 26 26" aria-hidden="true"><circle cx="13" cy="13" r="13" fill="var(--green)"/><rect x="6" y="8" width="14" height="10" fill="#fff"/><path d="M6 8l7 6 7-6" fill="none" stroke="var(--green)" stroke-width="1.4"/></svg>
      desmond@veldtmoorcapital.ventures
    </li>
  </ul>

  <p class="address">187 Fenworth St San Francisco, CA 94187</p>
</main>
</body>
</html>
```